Business Card Design Project

Business Card
We are rebranding with a new logo
Industry/Entity Type
Business
Contact Information for Business Card
Dennis Morvale +61 487215963 dennis@quorv.com.au P.O. Box 872 Fernlow QLD 4309
Requirements
Must have
- Logo

```html
<!DOCTYPE html>
<html lang="en">
<head>
<meta charset="utf-8">
<title>Quorv International – Business Card</title>
<link rel="stylesheet" href="https://fonts.googleapis.com/css2?family=Roboto:wght@400;500;700&display=swap">
<style>
  :root {
    --page-bg: #e6e6e4;
    --card-bg: #f3f3f2;
    --brand-blue: #1b94cc;
    --text-grey: #4a4a4a;
    --icon-blue: #1b8fc6;
  }
  * { margin: 0; padding: 0; box-sizing: border-box; }
  html, body {
    width: 1200px;
    height: 960px;
    overflow: hidden;
    background: var(--page-bg);
    font-family: "Roboto", Arial, sans-serif;
  }
  .business-card {
    position: absolute;
    left: 75px;
    top: 181px;
    width: 1050px;
    height: 598px;
    background: var(--card-bg);
    border-radius: 30px;
  }
  .holder-name {
    position: absolute;
    left: 74px;
    top: 138px;
    font-size: 31px;
    font-weight: 500;
    color: var(--brand-blue);
    letter-spacing: 0.2px;
  }
  .postal-address {
    position: absolute;
    left: 74px;
    top: 285px;
    font-size: 24px;
    line-height: 31px;
    color: var(--text-grey);
    font-style: normal;
  }
  .contact-list {
    position: absolute;
    left: 74px;
    top: 361px;
    list-style: none;
  }
  .contact-item {
    display: flex;
    align-items: center;
    height: 33px;
    font-size: 24px;
    color: var(--text-grey);
  }
  .contact-icon {
    width: 22px;
    height: 22px;
    margin-right: 18px;
    flex: none;
    fill: var(--icon-blue);
  }
  .brand-name {
    position: absolute;
    left: 520px;
    top: 170px;
    width: 450px;
    text-align: center;
    font-weight: 500;
    color: var(--brand-blue);
  }
  .brand-name .brand-word {
    display: block;
    font-size: 128px;
    line-height: 1;
    letter-spacing: 2px;
  }
  .brand-name .brand-sub {
    display: block;
    margin-top: 26px;
    font-size: 38px;
    letter-spacing: 5px;
  }
</style>
</head>
<body>
  <section class="business-card">
    <h1 class="holder-name">DENNIS MORVALE</h1>

    <address class="postal-address">
      P.O. Box 872<br>
      Fernlow QLD 4309
    </address>

    <ul class="contact-list">
      <li class="contact-item">
        <svg class="contact-icon" viewBox="0 0 24 24" aria-hidden="true">
          <path d="M6.6 10.8c1.4 2.8 3.8 5.1 6.6 6.6l2.2-2.2c.3-.3.7-.4 1-.2 1.1.4 2.3.6 3.6.6.6 0 1 .4 1 1V20c0 .6-.4 1-1 1C10.6 21 3 13.4 3 4c0-.6.4-1 1-1h3.5c.6 0 1 .4 1 1 0 1.3.2 2.5.6 3.6.1.3 0 .7-.2 1z"/>
        </svg>
        +61 487215963
      </li>
      <li class="contact-item">
        <svg class="contact-icon" viewBox="0 0 24 24" aria-hidden="true">
          <path d="M2 5h20v14H2z M4 7v.5l8 5 8-5V7l-8 5z" fill-rule="evenodd"/>
        </svg>
        dennis@quorv.com.au
      </li>
      <li class="contact-item">
        <svg class="contact-icon" viewBox="0 0 24 24" aria-hidden="true">
          <circle cx="12" cy="12" r="10"/>
          <path d="M7 8c2 0 3 1 3 3s2 2 2 4-1 3-1 4M15 5c-1 2 0 3 2 3s3 2 3 3" stroke="#f3f3f2" stroke-width="1.8" fill="none"/>
        </svg>
        www.quorv.com.au
      </li>
    </ul>

    <div class="brand-name">
      <span class="brand-word">Quorv</span>
      <span class="brand-sub">INTERNATIONAL</span>
    </div>
  </section>
</body>
</html>
```